Allied Health team of Physiotherapists & Occupational Therapists seek a business card design

We have our new logo, we now need our new business cards and stationary. Tidewell: Oedema & Family Clinic is seeking a generic card design to represent our whole team and individual cards for each therapist that incorporates our new logo to communicate our holistic approach that is calming, nuturing, supportive and welcoming.
Our Physiotherapists and Occupational Therapists assess, treat and provide education for people who are at risk of or who have lymphoedema. This is often as a result of treatment for cancer. We provide pre-operative and post-operative management and cancer rehabilitation in our Pilates studio. Our team also consists of Physiotherapists who have a strong interest in pelvic floor and continence management for both men and women.

Target Market(s)

Mainly women health conscious

Industry/Entity Type

Allied Health: Physiotherapy / Occupational Therapy

Contact Information for Business Card

Address: 14 Gallivant Ave Larkhaven 3277 Phone: 84316570 fax: 8431 6578 Email: info@tidewellcareservices.com.au Website: tidewellcareservices.com.au Facebook address: facebook.com/TidewellOedemaAndFamilyCareClinic. Room to write appointments. Individual cards need to have name, office email and individual email and professional details

Requirements
Must have
• Logo as per uploaded documents

```html
<!DOCTYPE html>
<html lang="en">
<head>
<meta charset="utf-8">
<title>Tidewell: Oedema & Family Clinic – Business Cards</title>
<link href="https://fonts.googleapis.com/css2?family=Lora:ital,wght@0,600;1,400&family=Roboto:wght@400&display=swap" rel="stylesheet">
<style>
  :root {
    --backdrop: #1f1f1f;
    --card: #efefef;
    --card-shade: #e4e4e4;
    --brand-orange: #e0875a;
    --ink: #2e2e2e;
    --ring: #e0875a;
  }
  * { margin: 0; padding: 0; box-sizing: border-box; }
  html, body { width: 1200px; height: 1138px; overflow: hidden; }
  body { background: var(--backdrop); position: relative; font-family: "Roboto", sans-serif; }

  .card {
    position: absolute;
    width: 620px;
    height: 374px;
    border-radius: 14px;
    background: linear-gradient(180deg, var(--card) 0%, var(--card-shade) 100%);
    overflow: hidden;
  }
  .card--front { left: 274px; top: 186px; }
  .card--back  { left: 276px; top: 608px; }

  .brand-mark {
    position: absolute;
    width: 250px;
    height: 250px;
    transform: translate(-50%, -50%) rotate(90deg);
    display: flex;
    align-items: center;
    justify-content: center;
  }
  .card--front .brand-mark { left: 311px; top: 190px; }
  .card--back .brand-mark { left: 435px; top: 148px; width: 210px; height: 210px; }
  .brand-mark__ring {
    position: absolute; inset: 0;
    border: 2px solid var(--ring);
    border-radius: 50%;
  }
  .brand-mark__name {
    font-family: "Lora", serif;
    font-weight: 600;
    color: var(--brand-orange);
    text-align: center;
    line-height: 1.25;
    font-size: 17px;
    letter-spacing: 0.5px;
  }
  .brand-mark__name .lead { display: block; font-size: 36px; letter-spacing: 1px; margin-bottom: 4px; }
  .card--back .brand-mark__name { font-size: 14px; }
  .card--back .brand-mark__name .lead { font-size: 30px; }

  .contact-block {
    position: absolute;
    left: 250px;
    top: 40px;
    width: 380px;
    transform-origin: top left;
    transform: rotate(90deg);
    color: var(--ink);
  }
  .person__name {
    font-family: "Lora", serif;
    font-weight: 600;
    color: var(--brand-orange);
    font-size: 19px;
    line-height: 22px;
  }
  .person__role { font-family: "Lora", serif; font-style: italic; font-size: 14px; line-height: 19px; }
  .person__focus { font-size: 14px; line-height: 19px; }
  .contact-list { list-style: none; margin-top: 20px; }
  .contact-list li {
    display: flex; align-items: center; gap: 12px;
    font-size: 15px; line-height: 23px;
    white-space: nowrap;
  }
  .contact-list svg { width: 13px; height: 13px; flex: none; fill: var(--brand-orange); }
  .contact-list .spacer { width: 22px; }
</style>
</head>
<body>

  <section class="card card--front" aria-label="Card front">
    <div class="brand-mark">
      <div class="brand-mark__ring"></div>
      <p class="brand-mark__name"><span class="lead">Tidewell</span>Oedema &amp; Family Clinic</p>
    </div>
  </section>

  <section class="card card--back" aria-label="Card back">
    <div class="contact-block">
      <h1 class="person__name">Maren Holt</h1>
      <p class="person__role">Physiotherapist</p>
      <p class="person__focus">Lymphoedema &amp; Oncology Rehabilitation</p>
      <p class="person__focus">Continence &amp; Pelvic Floor</p>
      <ul class="contact-list">
        <li>
          <svg viewBox="0 0 16 16" aria-label="Phone"><path d="M3 1h3l1.5 4-2 1.2a9 9 0 0 0 4.3 4.3L11 8.5l4 1.5v3a2 2 0 0 1-2 2A13 13 0 0 1 1 3a2 2 0 0 1 2-2z"/></svg>
          <span>8431 6570</span>
          <span class="spacer"></span>
          <svg viewBox="0 0 16 16" aria-label="Fax"><rect x="1" y="6" width="14" height="8" rx="1.5"/><rect x="4" y="1" width="8" height="6"/></svg>
          <span>8431 6578</span>
        </li>
        <li>
          <svg viewBox="0 0 16 16" aria-label="Email"><path d="M1 3h14v10H1z M2 4l6 5 6-5" /></svg>
          <span>info@tidewellcareservices.com.au</span>
        </li>
        <li>
          <svg viewBox="0 0 16 16" aria-label="Website"><circle cx="8" cy="8" r="7"/></svg>
          <span>www.tidewellcareservices.com.au</span>
        </li>
        <li>
          <svg viewBox="0 0 16 16" aria-label="Address"><path d="M8 0a5.5 5.5 0 0 1 5.5 5.5C13.5 10 8 16 8 16S2.5 10 2.5 5.5A5.5 5.5 0 0 1 8 0zm0 3.5a2 2 0 1 0 0 4 2 2 0 0 0 0-4z"/></svg>
          <span>14 Gallivant Ave, Larkhaven 3277</span>
        </li>
      </ul>
    </div>
    <div class="brand-mark">
      <div class="brand-mark__ring"></div>
      <p class="brand-mark__name"><span class="lead">Tidewell</span>Oedema &amp; Family Clinic</p>
    </div>
  </section>

</body>
</html>
```